Varelko App for Smart Devices IoT WiFi Electronic

Varelko is a siren manufacturer. This application is used for the company's products that have a Wi-Fi connection and an internet connection, which can be configured and activated remotely through this application. In addition, this application is used to activate the siren at specific times for the start and end of shifts in companies and schools. Users will be siren installers and IT or HR managers.
In addition to activating motorized sirens timers, some siren models have speakers and allow you to play TTS (text to speech) audio, audio recorded by the user on the phone and upload audio (mp3) with playlist programming with start and end times.
Application screens: home with dashboard (one dashboard for each category). Device categories: timers, speakers, motorized siren. Screen for requesting evaluation in the Play Store. Screen for registering the user profile. Screen for registering devices according to their category (timers, speakers, motorized siren). Screen for registering device groups. Screen for pairing the device on the client's Wi-Fi network. Screen for registering activation times. Screen for uploading MP3 audios. Screen for registering playlists with audio selection, start and end times. Screen for recording audio for later sending to the speakers. Screen for converting text to speech and sending to the speakers. It is important to have a time picker with the day of the week to program the activation times and playlist.

Target Market(s)

Schools, Companies and Stores.

Industry/Entity Type

IoT

Font styles to use
Sans Serif
Other font styles liked:
• roboto

Colors
FFC000
F8CF3A
FAE287
FDF2CF
FEFAEE

Requirements
Must have
• time picker with weekdays for timer programming feature.
Nice to have
• app review request screen on play store

```html
<!DOCTYPE html>
<html lang="en">
<head>
<meta charset="utf-8">
<title>Dashboard</title>
<link href="https://fonts.googleapis.com/css2?family=Roboto:wght@400;500;700&display=swap" rel="stylesheet">
<style>
  :root {
    --amber: #FFC000;
    --sun: #F8CF3A;
    --sun-deep: #F4C21A;
    --tab: #F2BE14;
    --butter: #FAE287;
    --cream: #FDF2CF;
    --ivory: #FEFAEE;
    --ink: #3B4260;
    --muted: #9A9A9A;
    --white: #FFFFFF;
    --page: #FFFFFF;
  }
  * { box-sizing: border-box; margin: 0; padding: 0; }
  html, body {
    width: 1200px; height: 2181px; overflow: hidden;
    background: var(--page);
    font-family: "Roboto", sans-serif;
  }
  .stage {
    position: absolute; left: 0; top: 0;
    width: 520px; height: 945px;
    transform: scale(2.3077); transform-origin: 0 0;
  }
  .screen {
    position: absolute; left: 72px; top: 58px;
    width: 376px; height: 820px;
    border-radius: 38px; overflow: hidden;
    background: linear-gradient(180deg, var(--ivory) 0%, var(--white) 70%);
    box-shadow: 0 0 0 1px #eee;
  }
  .hero { position: absolute; left: 0; top: 0; width: 376px; height: 330px; }
  .status {
    position: absolute; top: 10px; left: 22px; right: 22px;
    display: flex; justify-content: space-between; align-items: center;
    color: var(--white); font-size: 12px; font-weight: 700;
  }
  .topbar {
    position: absolute; top: 46px; left: 0; width: 100%; height: 26px;
    display: flex; align-items: center; justify-content: space-between;
    padding: 0 22px;
  }
  .topbar h1 {
    color: var(--white); font-size: 18px; font-weight: 700;
    position: absolute; left: 0; right: 0; text-align: center; pointer-events: none;
  }
  .welcome {
    position: absolute; top: 106px; width: 100%; text-align: center;
    color: var(--white); font-weight: 500;
  }
  .welcome .line1 { font-size: 16px; line-height: 22px; }
  .welcome .line2 { font-size: 18px; line-height: 34px; }
  .search {
    position: absolute; left: 19px; top: 183px; width: 338px; height: 42px;
    background: rgba(255,255,255,0.92); border-radius: 10px;
    display: flex; align-items: center; gap: 10px; padding-left: 16px;
    color: var(--muted); font-size: 12px;
  }
  .category {
    position: absolute; left: 19px; width: 338px; height: 90px;
    border-radius: 10px; background: var(--white);
    box-shadow: 0 4px 12px rgba(0,0,0,0.10);
  }
  .category.is-active { background: var(--sun-deep); }
  .category .art {
    position: absolute; left: 18px; top: 14px; width: 64px; height: 62px;
    border-radius: 14px;
  }
  .category .label {
    position: absolute; left: 110px; top: 0; line-height: 90px;
    font-size: 18px; font-weight: 700; color: var(--ink);
  }
  .category.is-active .label { color: var(--white); }
  .category .go {
    position: absolute; left: 285px; top: 31px; width: 28px; height: 28px;
    border: 1px solid var(--amber); border-radius: 4px;
    display: flex; align-items: center; justify-content: center;
  }
  .category.is-active .go { border-color: rgba(255,255,255,0.75); background: rgba(255,255,255,0.12); }
  .art-timers { background: linear-gradient(135deg, #CFE3F5 0%, #8DBBE6 100%); opacity: .9; }
  .art-speakers { background: linear-gradient(135deg, #CDEBC4 0%, #B9DCEF 100%); }
  .art-sirens { background: linear-gradient(135deg, #DCE7F6 0%, #B6CBEA 100%); }
  .tabbar {
    position: absolute; left: 11px; top: 737px; width: 355px; height: 68px;
    background: var(--tab); border-radius: 14px;
    display: flex; justify-content: space-around; align-items: center;
    padding: 0 8px;
  }
  .tab {
    width: 70px; display: flex; flex-direction: column; align-items: center; gap: 3px;
    color: rgba(255,255,255,0.7); font-size: 8px; font-weight: 500;
    position: relative;
  }
  .tab.is-current { color: var(--white); font-weight: 700; }
  .tab.is-current::after {
    content: ""; position: absolute; bottom: -12px; width: 36px; height: 3px;
    background: var(--white); border-radius: 2px;
  }
</style>
</head>
<body>
<div class="stage">
  <div class="screen">
    <svg class="hero" viewBox="0 0 376 330" aria-hidden="true">
      <defs>
        <linearGradient id="heroFill" x1="0" y1="0" x2="0" y2="1">
          <stop offset="0" stop-color="#F6C52C"/>
          <stop offset="1" stop-color="#F8CF3A"/>
        </linearGradient>
      </defs>
      <path d="M0 0H376V270C330 240 280 260 240 275C190 292 150 250 90 262C50 270 20 280 0 290Z" fill="url(#heroFill)"/>
      <path d="M376 90H312C300 110 330 140 376 150Z" fill="#F0D68A" opacity=".55"/>
      <path d="M0 90C40 90 60 120 40 150C20 175 0 170 0 200Z" fill="#F2D47A" opacity=".5"/>
    </svg>

    <div class="status">
      <span>09:41</span>
      <svg width="48" height="12" viewBox="0 0 48 12" aria-hidden="true">
        <rect x="0" y="8" width="2.5" height="3" fill="#333"/><rect x="4" y="6" width="2.5" height="5" fill="#333"/>
        <rect x="8" y="3" width="2.5" height="8" fill="#333"/>
        <path d="M20 5a7 7 0 0 1 9 0M22 7.5a4 4 0 0 1 5 0" stroke="#333" stroke-width="1.6" fill="none"/>
        <circle cx="24.5" cy="10" r="1.2" fill="#333"/>
        <rect x="33" y="2" width="13" height="8" rx="2" fill="#333"/>
      </svg>
    </div>

    <header class="topbar">
      <svg width="20" height="16" viewBox="0 0 20 16" aria-label="Menu">
        <path d="M1 2H19M1 8H19M1 14H19" stroke="#fff" stroke-width="2" stroke-linecap="round"/>
      </svg>
      <h1>Dashboard</h1>
      <svg width="18" height="18" viewBox="0 0 18 18" aria-label="Notifications">
        <path d="M4 13V8a5 5 0 0 1 10 0v5l1.5 1.5h-13Z" fill="none" stroke="#fff" stroke-width="1.5" stroke-linejoin="round"/>
        <path d="M7.5 16h3" stroke="#fff" stroke-width="1.5" stroke-linecap="round"/>
        <circle cx="13" cy="4" r="2" fill="#E23B3B"/>
      </svg>
    </header>

    <div class="welcome">
      <p class="line1">Welcome to</p>
      <p class="line2">Siren Alarm Application</p>
    </div>

    <div class="search">
      <svg width="18" height="18" viewBox="0 0 18 18" aria-hidden="true">
        <circle cx="8" cy="8" r="6.5" fill="none" stroke="#999" stroke-width="1.5"/>
        <path d="M13 13l4 4" stroke="#999" stroke-width="1.5" stroke-linecap="round"/>
      </svg>
      <span>Search</span>
    </div>

    <div class="category is-active" style="top:249px">
      <div class="art art-timers" role="img" aria-label="Illustration of a wall clock"></div>
      <span class="label">Timers</span>
      <span class="go"><svg width="12" height="12" viewBox="0 0 12 12" aria-hidden="true"><path d="M1 6H11M7 2l4 4-4 4" stroke="#fff" stroke-width="1.2" fill="none"/></svg></span>
    </div>

    <div class="category" style="top:359px">
      <div class="art art-speakers" role="img" aria-label="Illustration of a megaphone with gears"></div>
      <span class="label">Speakers</span>
      <span class="go"><svg width="12" height="12" viewBox="0 0 12 12" aria-hidden="true"><path d="M1 6H11M7 2l4 4-4 4" stroke="#FFC000" stroke-width="1.2" fill="none"/></svg></span>
    </div>

    <div class="category" style="top:469px">
      <div class="art art-sirens" role="img" aria-label="Illustration of a calendar with a check mark"></div>
      <span class="label">Motorized Sirens</span>
      <span class="go"><svg width="12" height="12" viewBox="0 0 12 12" aria-hidden="true"><path d="M1 6H11M7 2l4 4-4 4" stroke="#FFC000" stroke-width="1.2" fill="none"/></svg></span>
    </div>

    <nav class="tabbar">
      <div class="tab is-current">
        <svg width="18" height="18" viewBox="0 0 18 18" aria-hidden="true"><path d="M3 8l6-5 6 5v8H3Z M3 11h12" fill="none" stroke="#fff" stroke-width="1.6" stroke-linejoin="round"/></svg>
        <span>Home</span>
      </div>
      <div class="tab">
        <svg width="18" height="18" viewBox="0 0 18 18" aria-hidden="true"><circle cx="9" cy="9" r="7" fill="rgba(255,255,255,.7)"/><path d="M9 2V9H16" stroke="#F2BE14" stroke-width="1.4" fill="none"/></svg>
        <span>Devices</span>
      </div>
      <div class="tab">
        <svg width="18" height="18" viewBox="0 0 18 18" aria-hidden="true"><path d="M2 2V16H16M4 13l4-5 3 3 5-6" fill="none" stroke="rgba(255,255,255,.7)" stroke-width="1.4"/></svg>
        <span>Settings</span>
      </div>
      <div class="tab">
        <svg width="18" height="18" viewBox="0 0 18 18" aria-hidden="true"><circle cx="9" cy="6" r="4" fill="none" stroke="rgba(255,255,255,.7)" stroke-width="1.4"/><path d="M2 17c1-4 4-6 7-6s6 2 7 6" fill="none" stroke="rgba(255,255,255,.7)" stroke-width="1.4"/></svg>
        <span>Profile</span>
      </div>
    </nav>
  </div>
</div>
</body>
</html>
```